Website Design for an Exciting & Sophisticated Premium CBD Company.

Design a responsive Website with the following goals in mind:
-      Main theme for the site will be based on the Tall Harbor Windmere theme.  Please use this when designing for ease of integration.  You can see our current site to gain more insight.  fennocbd.com
-	Build trust with website visitors with an engaging, informative content driven website, that leads to a conversion of product purchase and repeat business.
-	The website will embody a lifestyle feel and make the visitor identify with the content or emphasize with the life they used to have or believe they can have by using our products
-	The website will allow for super charged SEO and other digital marketing and advertising strategies and tactics used to increase discovery, awareness, and conversion.
Please see additional goals in the uploaded files.

Target Market(s)
Male/Female 25-50
Number of Pages Required
1 page
Font styles to use
Other font styles liked:
- Monserrat is the company Font. Please use throughout. Regular, Bold, Semi-Bold, light
Requirements
Must have
- Please see attached document for this information
Nice to have
Should not have

```html
<!DOCTYPE html>
<html lang="en">
<head>
<meta charset="utf-8">
<title>FENNO CBD</title>
<link href="https://fonts.googleapis.com/css2?family=Montserrat:wght@300;400;500;600;700&family=Lato:wght@400;700&display=swap" rel="stylesheet">
<style>
:root{
  --black:#000;
  --white:#fff;
  --gold:#d6b463;
  --gold-band:#d9ba6a;
  --ink:#1b1b1b;
  --muted:#6c6c6c;
  --card-bg:#f4f4f4;
  --star:#c9d41c;
}
*{box-sizing:border-box;margin:0;padding:0}
html,body{width:1200px;height:3460px;overflow:hidden}
body{position:relative;font-family:"Montserrat",sans-serif;color:var(--ink);background:var(--white)}
.abs{position:absolute}

/* header */
.site-header{left:0;top:0;width:1200px;height:124px;background:var(--black)}
.main-nav{left:111px;top:50px;display:flex;gap:28px}
.main-nav a,.util-nav a{color:var(--white);text-decoration:none;font-family:"Lato",sans-serif;font-weight:700;font-size:19px}
.brand{left:540px;top:18px;width:120px;text-align:center;color:var(--gold);font-weight:500}
.brand-dot{width:38px;height:38px;border-radius:50%;background:var(--gold);margin:0 auto 10px}
.brand-name{font-size:20px;letter-spacing:2px;line-height:1}
.brand-sub{font-size:10px;letter-spacing:2px;margin-top:3px}
.util-nav{left:895px;top:50px;display:flex;align-items:center;gap:24px}
.util-nav svg{display:block}

/* hero */
.hero{left:0;top:124px;width:1200px;height:598px;
  background:linear-gradient(100deg,#e0253a 0%,#ec3b2c 30%,#f05a22 45%,#f7862a 60%,#f9a43a 80%,#fbb84f 100%)}
.hero-title{left:110px;top:318px;color:var(--white);font-weight:700;font-size:40px}
.hero-text{left:110px;top:383px;width:330px;color:var(--white);font-size:22px;line-height:32px}
.btn-outline{border:2px solid var(--white);color:var(--white);font-weight:700;display:flex;align-items:center;justify-content:center;text-decoration:none}
.hero-btn{left:112px;top:473px;width:129px;height:42px;font-size:18px}
.hero-dots{left:42px;top:393px;display:flex;flex-direction:column;gap:7px}
.hero-dots span{width:11px;height:11px;border-radius:50%;border:1.5px solid var(--white)}
.hero-dots span.on{background:var(--white)}

/* promo tiles */
.promo{top:722px;width:600px;height:342px;text-align:center;color:var(--white)}
.promo-kids{left:0;background:linear-gradient(135deg,#b9b2a6,#8a7a66 50%,#c9b49a)}
.promo-drops{left:600px;background:linear-gradient(135deg,#5c6a78,#3d4650 50%,#8a7460)}
.promo-title{position:absolute;left:0;right:0;top:100px;font-weight:600;font-size:23px}
.promo-sub{position:absolute;left:0;right:0;top:148px;font-family:"Lato",sans-serif;font-size:15px}
.promo-btn{position:absolute;left:242px;top:193px;width:116px;height:42px;font-size:16px}

/* featured */
.section-title{left:0;width:1200px;text-align:center;font-weight:700;font-size:38px;color:var(--ink)}
.section-title em{font-style:normal;color:var(--gold)}
.featured-title{top:1148px}
.product{top:1239px;width:308px;height:361px;background:var(--white);box-shadow:0 1px 8px rgba(0,0,0,.08);text-align:center}
.product-shot{height:226px;background:var(--card-bg);display:flex;align-items:center;justify-content:center}
.product-shot .shape{background:linear-gradient(#2a2a2a,#111);border-radius:10px}
.product-name{margin-top:30px;font-weight:500;font-size:17px}
.product-price{margin-top:14px;font-family:"Lato",sans-serif;color:var(--muted);font-size:15px}
.product-link{margin-top:14px;color:var(--gold);font-weight:600;font-size:15px}
.arrow{width:35px;height:35px;border-radius:50%;border:1.5px solid var(--gold);display:flex;align-items:center;justify-content:center}

/* about */
.about{left:0;top:1690px;width:1200px;height:402px;
  background:linear-gradient(90deg,#c98a2c 0%,#b5642a 30%,#d9a253 55%,#e8b062 70%,#c44a2a 100%)}
.about-panel{left:112px;top:1736px;width:488px;height:356px;background:rgba(70,60,40,.55);color:var(--white);padding:0 32px}
.about-panel h2{margin-top:28px;font-size:29px;font-weight:700}
.about-panel p{margin-top:18px;font-size:15px;line-height:26px;text-align:justify}
.btn-gold{display:flex;align-items:center;justify-content:center;background:var(--gold);color:var(--white);font-weight:700;font-size:18px;outline:2px solid #efdca8;outline-offset:-5px}
.about-btn{width:133px;height:46px;margin-top:30px}

/* why */
.why{left:0;top:2092px;width:1200px;height:312px;
  background:linear-gradient(100deg,#d9478a 0%,#d351a8 40%,#c85bd0 70%,#8b4fd4 100%)}
.why-title{left:0;top:2130px;width:1200px;text-align:center;color:var(--white);font-weight:700;font-size:36px}
.feature{top:2205px;width:210px;text-align:center;color:var(--white);font-size:20px;line-height:30px;font-weight:500}
.feature svg{display:block;margin:0 auto 22px}

/* reviews */
.reviews-title{top:2468px}
.review{top:2554px;width:473px;height:294px;background:var(--white);box-shadow:0 1px 10px rgba(0,0,0,.08);text-align:center}
.quote{margin-top:14px;color:var(--gold);font-size:70px;font-weight:700;line-height:60px;height:44px;font-family:"Lato",sans-serif}
.review p{margin:22px auto 0;width:310px;color:var(--muted);font-size:15px;line-height:26px}
.stars{margin-top:8px;color:var(--star);font-size:14px;letter-spacing:2px}
.avatar{width:62px;height:62px;border-radius:50%;margin:12px auto 0}
.reviewer{margin-top:10px;font-size:19px;font-weight:500}

/* newsletter */
.newsletter{left:0;top:2940px;width:1200px;height:171px;background:var(--gold-band);text-align:center;color:var(--white)}
.newsletter h2{margin-top:24px;font-size:27px;font-weight:700}
.newsletter p{margin-top:10px;font-size:15px;color:#f6ecd2}
.signup{left:340px;top:3046px;width:520px;height:42px;display:flex;border:2px solid var(--white);background:var(--white)}
.signup .field{flex:1;display:flex;align-items:center;padding-left:13px;font-family:"Lato",sans-serif;font-size:15px;color:#666}
.signup .send{width:112px;background:var(--gold-band);color:var(--white);font-weight:700;font-size:15px;display:flex;align-items:center;justify-content:center}

/* footer */
.site-footer{left:0;top:3111px;width:1200px;height:349px;background:var(--black);color:var(--white)}
.footer-brand{left:104px;top:3175px;width:120px;text-align:center;color:var(--gold);font-weight:500}
.footer-col{top:3172px}
.footer-col h3{font-size:19px;font-weight:500;margin-bottom:20px}
.footer-col li{list-style:none;font-size:15px;line-height:24px}
.contact-row{display:flex;gap:14px;font-size:15px;line-height:22px;margin-bottom:10px}
.contact-row svg{flex:none;margin-top:3px}
.footer-rule{left:111px;top:3408px;width:977px;height:1px;background:#555}
.copyright{left:111px;top:3425px;font-size:12px}
.cards{left:836px;top:3421px;display:flex;gap:4px}
.cards span{width:45px;height:27px;border-radius:3px;background:#e8e8e8}
</style>
</head>
<body>

<header class="abs site-header"></header>
<nav class="abs main-nav"><a href="#">Shop</a><a href="#">Drops</a><a href="#">Topicals</a></nav>
<div class="abs brand">
  <div class="brand-dot"></div>
  <div class="brand-name">FENNO</div>
  <div class="brand-sub">CBD</div>
</div>
<nav class="abs util-nav">
  <a href="#">Blog</a>
  <svg width="20" height="20" viewBox="0 0 20 20"><circle cx="8" cy="8" r="6" fill="none" stroke="#fff" stroke-width="2.6"/><path d="M12.5 12.5L18 18" stroke="#fff" stroke-width="3"/></svg>
  <svg width="22" height="22" viewBox="0 0 22 22"><circle cx="11" cy="11" r="9.5" fill="none" stroke="#fff" stroke-width="2"/><circle cx="11" cy="8.5" r="3.5" fill="#fff"/><path d="M4.5 17.5c2-4 11-4 13 0" fill="#fff"/></svg>
  <svg width="24" height="22" viewBox="0 0 24 22"><path d="M1 3h4l3 11h11l2-8H6.5" fill="none" stroke="#fff" stroke-width="2.4"/><circle cx="9" cy="18" r="2" fill="#fff"/><circle cx="18" cy="18" r="2" fill="#fff"/><circle cx="20" cy="3" r="3" fill="var(--gold)"/></svg>
</nav>

<section class="abs hero" role="img" aria-label="Photo: dropper bottles in front of a woman raising her arms against a sunset"></section>
<h1 class="abs hero-title">FENNO CBD</h1>
<p class="abs hero-text">FENNO CBD was born out of a drive for a better</p>
<a class="abs btn-outline hero-btn" href="#">Shop Now</a>
<div class="abs hero-dots"><span></span><span></span><span class="on"></span><span></span></div>

<section class="abs promo promo-kids" role="img" aria-label="Photo: children sharing a meal at a table">
  <h2 class="promo-title">Creativity is Calling</h2>
  <p class="promo-sub">Our most popular profile is back in stock.</p>
  <a class="btn-outline promo-btn" href="#">Shop Now</a>
</section>
<section class="abs promo promo-drops" role="img" aria-label="Photo: a woman adding oil drops to a drink">
  <h2 class="promo-title">ICE CREAM DROPS ANYONE?</h2>
  <p class="promo-sub">As delicious as real cookies &amp; cream.</p>
  <a class="btn-outline promo-btn" href="#">Shop Now</a>
</section>

<h2 class="abs section-title featured-title">Featured <em>Product</em></h2>
<div class="abs arrow" style="left:37px;top:1403px"><svg width="10" height="12" viewBox="0 0 10 12"><path d="M7 1L2 6l5 5" fill="none" stroke="var(--gold)" stroke-width="1.5"/></svg></div>
<div class="abs arrow" style="left:1136px;top:1403px"><svg width="10" height="12" viewBox="0 0 10 12"><path d="M3 1l5 5-5 5" fill="none" stroke="var(--gold)" stroke-width="1.5"/></svg></div>

<article class="abs product" style="left:112px">
  <div class="product-shot"><div class="shape" role="img" aria-label="Product photo: watermelon drops bottle" style="width:62px;height:200px"></div></div>
  <div class="product-name">Bright Mind - Watermelon Drops</div>
  <div class="product-price">$84.99</div>
  <div class="product-link">Shop Now &nbsp;»</div>
</article>
<article class="abs product" style="left:445px">
  <div class="product-shot"><div class="shape" role="img" aria-label="Product photo: salve stick" style="width:90px;height:200px;background:linear-gradient(90deg,#22252e 50%,#d8b84a)"></div></div>
  <div class="product-name">Warm Ember Salve Stick 2000MG</div>
  <div class="product-price">$114.99</div>
  <div class="product-link">Shop Now &nbsp;»</div>
</article>
<article class="abs product" style="left:778px">
  <div class="product-shot"><div class="shape" role="img" aria-label="Product photo: cherry drops bottle" style="width:66px;height:210px"></div></div>
  <div class="product-name">Be Easy - Cool Cherry Drops</div>
  <div class="product-price">$84.99</div>
  <div class="product-link">Shop Now &nbsp;»</div>
</article>

<section class="abs about" role="img" aria-label="Photo: smiling woman throwing autumn leaves in the air"></section>
<div class="abs about-panel">
  <h2>About Fenno CBD</h2>
  <p>FENNO CBD was born out of a drive for a better life. Created to enable the extraordinary in us all through the use of CBD. FENNO stands for fun, excitement, joy, and happiness, all the qualities that promote the best feeling and overall wellbeing.</p>
  <div class="btn-gold about-btn">Read More</div>
</div>

<section class="abs why"></section>
<h2 class="abs why-title">Why Choose Us?</h2>
<div class="abs feature" style="left:68px">
  <svg width="60" height="60" viewBox="0 0 60 60" fill="none" stroke="var(--gold)" stroke-width="2"><path d="M18 4h14M22 4v18L8 50h34L28 22V4"/><path d="M40 10h10M42 10v40h6V10"/><circle cx="20" cy="42" r="3"/><circle cx="30" cy="38" r="2"/></svg>
  3rd Party Lab<br>Tested
</div>
<div class="abs feature" style="left:277px">
  <svg width="60" height="60" viewBox="0 0 60 60" fill="none" stroke="var(--gold)" stroke-width="2.5"><circle cx="30" cy="30" r="27"/><path d="M24 42V18h9a7 7 0 010 14h-9"/></svg>
  Free of Pesticides<br>Solvents
</div>
<div class="abs feature" style="left:486px">
  <svg width="64" height="60" viewBox="0 0 64 60" fill="none" stroke="var(--gold)" stroke-width="2"><path d="M32 4l8 5v9l-8 5-8-5V9z"/><path d="M14 30l8 5v9l-8 5-8-5v-9z"/><path d="M50 30l8 5v9l-8 5-8-5v-9z"/><path d="M32 26v20M22 36h20M25 29l14 14M39 29L25 43"/></svg>
  Broad Spestrum<br>Hemp CBD
</div>
<div class="abs feature" style="left:696px">
  <svg width="60" height="60" viewBox="0 0 60 60" fill="none" stroke="var(--gold)" stroke-width="2.5"><circle cx="30" cy="30" r="27"/><path d="M11 11l38 38"/><path d="M22 40c0-12 8-20 18-22-2 10-8 18-18 22zM30 44V30"/></svg>
  Non GMO
</div>
<div class="abs feature" style="left:904px">
  <svg width="60" height="60" viewBox="0 0 60 60" fill="none" stroke="var(--gold)" stroke-width="2.5"><circle cx="30" cy="30" r="27"/><path d="M30 3v54M30 16h25M30 30h27M30 44h25"/><circle cx="17" cy="20" r="3"/><circle cx="17" cy="38" r="3"/></svg>
  100% Sourced<br>Made in the USA
</div>

<h2 class="abs section-title reviews-title">People <em>Reviews</em></h2>
<div class="abs arrow" style="left:36px;top:2680px"><svg width="10" height="12" viewBox="0 0 10 12"><path d="M7 1L2 6l5 5" fill="none" stroke="var(--gold)" stroke-width="1.5"/></svg></div>
<div class="abs arrow" style="left:1126px;top:2680px"><svg width="10" height="12" viewBox="0 0 10 12"><path d="M3 1l5 5-5 5" fill="none" stroke="var(--gold)" stroke-width="1.5"/></svg></div>

<article class="abs review" style="left:112px">
  <div class="quote">“</div>
  <p>Lorem ipsum dolor sit amet, consectetur adipiscing elit, sed do eiusmod tempor incididunt ut laboreullamco.</p>
  <div class="stars">★★★★★</div>
  <div class="avatar" role="img" aria-label="Portrait photo of the reviewer" style="background:linear-gradient(#cfc6bd,#6d5a4c)"></div>
  <div class="reviewer">Marisol</div>
</article>
<article class="abs review" style="left:614px">
  <div class="quote">“</div>
  <p>Lorem ipsum dolor sit amet, consectetur adipiscing elit, sed do eiusmod tempor incididunt ut laboreullamco.</p>
  <div class="stars">★★★★★</div>
  <div class="avatar" role="img" aria-label="Portrait photo of the reviewer" style="background:linear-gradient(#dfe6ee,#8193a8)"></div>
  <div class="reviewer">Derek Lane</div>
</article>

<section class="abs newsletter">
  <h2>Subscribe Our Newsletter</h2>
  <p>Get the latest updates on new products and upcoming sales</p>
</section>
<div class="abs signup"><div class="field">Email Address</div><div class="send">Subscribe</div></div>

<footer class="abs site-footer"></footer>
<div class="abs footer-brand">
  <div class="brand-dot" style="width:48px;height:48px;margin-bottom:14px"></div>
  <div class="brand-name">FENNO</div>
  <div class="brand-sub">CBD</div>
</div>
<div class="abs footer-col" style="left:372px;color:#fff">
  <h3>Quick Links</h3>
  <ul><li>Home</li><li>Shop</li><li>Drops</li><li>Topicals</li><li>Contact Us</li></ul>
</div>
<div class="abs footer-col" style="left:638px;color:#fff">
  <h3>About</h3>
  <ul><li>Privacy Policy</li><li>Terms &amp; Conditions</li><li>Shipping &amp; Returns</li><li>Sitemap</li></ul>
</div>
<div class="abs footer-col" style="left:904px;color:#fff">
  <h3>Contact Us</h3>
  <div class="contact-row"><svg width="12" height="16" viewBox="0 0 12 16"><path d="M6 0a6 6 0 016 6c0 4-6 10-6 10S0 10 0 6a6 6 0 016-6z" fill="var(--gold)"/><circle cx="6" cy="6" r="2" fill="#000"/></svg><span>4210 Linden Row<br>Alder TX 75990</span></div>
  <div class="contact-row"><svg width="14" height="14" viewBox="0 0 14 14"><path d="M3 0l3 3-2 2c1 2 3 4 5 5l2-2 3 3-2 3C6 14 0 8 0 2z" fill="var(--gold)"/></svg><span>555 014 2290</span></div>
  <div class="contact-row"><svg width="15" height="12" viewBox="0 0 15 12"><rect width="15" height="12" fill="var(--gold)"/><path d="M0 0l7.5 6L15 0" fill="none" stroke="#000" stroke-width="1.3"/></svg><span>info@fennocbd.in</span></div>
</div>
<div class="abs footer-rule"></div>
<div class="abs copyright" style="color:#fff">Copyrights 2020 FENNO CBD. All rights reserved</div>
<div class="abs cards"><span></span><span></span><span></span><span></span><span></span></div>

</body>
</html>
```